Four in One (Flexible infographic for Content Management Industry)

See attachment.
A graphic depicting 4 products, where each can stand on its own and each can be combined with others, but where, if all are taken together, the best result is achieved (the "super product").
Intended use is web. See attached file as an example.
The most basic idea is as the attached diagram shows, where 4 rectangles are arranged in a quadrangle, with a middle rectangle in the center representing the combined 4 products. This concept is fine except it is a bit too obvious as it stands. We are looking for either a variation of this or another concept.
The audience is technical + professional + enterprise - NOT consumers. Hence the design should be conservative in nature.
We are aware of tools like as Canva or Pictogram where such graphics are available, but we are looking for something with a bit more imagination and flexibility.
This graphic should be targeted to web sites and be delivered with vector-based (SVG) graphics.

```html
<!DOCTYPE html>
<html lang="en">
<head>
<meta charset="utf-8">
<title>Four in One – Super Product</title>
<link href="https://fonts.googleapis.com/css2?family=Poppins:wght@400;700;800&display=swap" rel="stylesheet">
<style>
:root{
  --bg:#b5b5b5;
  --card:#ffffff;
  --ink:#2a2a2a;
  --heading:#3b3b3b;
  --doc:#e8a200;
  --sec:#e01515;
  --erp:#4b8a1b;
  --dig:#2d51ae;
  --hub:#f6ab0d;
  --ring:#e6e6e6;
}
*{margin:0;padding:0;box-sizing:border-box}
html,body{width:1200px;height:956px;overflow:hidden;background:var(--bg);font-family:"Poppins",sans-serif;color:var(--ink)}
.canvas{position:relative;width:1200px;height:956px}
.card{position:absolute;width:481px;height:299px;background:var(--card);box-shadow:6px 10px 14px rgba(0,0,0,.28)}
.card--doc{left:100px;top:163px;border-radius:0 60px 0 60px}
.card--sec{left:618px;top:163px;border-radius:60px 0 60px 0}
.card--erp{left:100px;top:493px;border-radius:60px 0 60px 0}
.card--dig{left:618px;top:493px;border-radius:60px 60px 0 60px}
.content{position:absolute;top:27px;width:420px}
.card--doc .content,.card--erp .content{left:51px}
.card--sec .content,.card--dig .content{right:51px;text-align:right}
.title{font-weight:800;font-size:24.5px;line-height:24px;color:var(--heading);letter-spacing:.2px}
.title span{display:block}
.card--doc .accent{color:var(--doc)}
.card--sec .accent{color:var(--sec)}
.card--erp .accent{color:var(--erp)}
.card--dig .accent{color:var(--dig)}
.lead{margin-top:20px;font-weight:700;font-size:14.4px;line-height:17.3px;white-space:nowrap}
.features{list-style:none;margin-top:8px;font-size:13.6px;line-height:19.3px}
.features li{display:flex;align-items:center;gap:6px}
.card--sec .features li,.card--dig .features li{justify-content:flex-end}
.tick{width:12px;height:12px;flex:none}
.card--sec .features li .tick,.card--dig .features li .tick{order:2}
.btn{position:absolute;top:235px;width:129px;height:33px;border-radius:17px;color:#fff;font-weight:700;font-size:15px;line-height:33px;text-align:center;text-decoration:none}
.card--doc .btn{left:50px;background:var(--doc)}
.card--sec .btn{right:51px;background:var(--sec)}
.card--erp .btn{left:50px;background:var(--erp)}
.card--dig .btn{right:51px;background:var(--dig)}
.art{position:absolute;width:90px;height:86px;border-radius:8px;background:linear-gradient(135deg,#f3f3f3,#ebebeb)}
.card--doc .art{left:355px;top:179px}
.card--sec .art{left:35px;top:173px}
.card--erp .art{left:356px;top:176px}
.card--dig .art{left:26px;top:176px}
.hub-ring{position:absolute;left:497px;top:369px;width:204px;height:204px;border-radius:50%;background:var(--ring)}
.hub{position:absolute;left:513px;top:385px;width:172px;height:172px;border-radius:50%;background:var(--hub);box-shadow:4px 8px 12px rgba(0,0,0,.3);display:flex;align-items:center;justify-content:center;text-align:center}
.hub-label{font-weight:800;font-size:31px;line-height:27px;color:#111;-webkit-text-stroke:5px #fff;paint-order:stroke fill;margin-top:-6px}
</style>
</head>
<body>
<svg width="0" height="0" style="position:absolute" aria-hidden="true">
  <symbol id="tick" viewBox="0 0 12 12"><circle cx="6" cy="6" r="6" fill="currentColor"/><path d="M3.2 6.2l1.9 1.9 3.7-3.8" fill="none" stroke="#fff" stroke-width="1.6" stroke-linecap="round" stroke-linejoin="round"/></symbol>
</svg>
<main class="canvas">

  <section class="card card--doc">
    <div class="content">
      <h2 class="title"><span>DOCUMENT</span><span class="accent">MANAGEMENT</span></h2>
      <p class="lead">Streamline document organization, access, &amp;<br>collaboration with easier</p>
      <ul class="features">
        <li><svg class="tick" style="color:var(--doc)"><use href="#tick"/></svg>Centralized Document Control</li>
        <li><svg class="tick" style="color:var(--doc)"><use href="#tick"/></svg>Collaborative Workspace Integration</li>
        <li><svg class="tick" style="color:var(--doc)"><use href="#tick"/></svg>Automated Compliance Tracking</li>
      </ul>
    </div>
    <div class="art" role="img" aria-label="Faint line illustration of documents in a file box"></div>
    <a class="btn" href="#">LEARN MORE</a>
  </section>

  <section class="card card--sec">
    <div class="content">
      <h2 class="title"><span>SECURITY &amp;</span><span class="accent">COMPLIANCE</span></h2>
      <p class="lead">Benefit from tailored cloud solutions, secure data<br>storage, and expert disaster recovery planning for<br>reliable and scalable IT operations</p>
      <ul class="features">
        <li><svg class="tick" style="color:var(--sec)"><use href="#tick"/></svg>Custom Cloud Solutions</li>
        <li><svg class="tick" style="color:var(--sec)"><use href="#tick"/></svg>Secure Data Storage</li>
        <li><svg class="tick" style="color:var(--sec)"><use href="#tick"/></svg>Expert Disaster Recovery</li>
      </ul>
    </div>
    <div class="art" role="img" aria-label="Faint line illustration of a security shield over a server"></div>
    <a class="btn" href="#">LEARN MORE</a>
  </section>

  <section class="card card--erp">
    <div class="content">
      <h2 class="title"><span>ENTERPRISE</span><span class="accent">RESOURCE PLANNING</span></h2>
      <p class="lead">Simplify management across finance, sales, &amp;<br>operations, enabling better decision-making &amp;<br>improved productivity.</p>
      <ul class="features">
        <li><svg class="tick" style="color:var(--erp)"><use href="#tick"/></svg>Integrated Business Processes</li>
        <li><svg class="tick" style="color:var(--erp)"><use href="#tick"/></svg>Enhanced Decision-Making</li>
        <li><svg class="tick" style="color:var(--erp)"><use href="#tick"/></svg>Productivity Improvement</li>
      </ul>
    </div>
    <div class="art" role="img" aria-label="Faint line illustration of a hand selecting connected team members"></div>
    <a class="btn" href="#">LEARN MORE</a>
  </section>

  <section class="card card--dig">
    <div class="content">
      <h2 class="title"><span>DIGITAL</span><span class="accent">TRANSFORMATION</span></h2>
      <p class="lead">Turn scanned documents into easily searchable<br>digital archives, boosting efficiency &amp; accessibility</p>
      <ul class="features">
        <li><svg class="tick" style="color:var(--dig)"><use href="#tick"/></svg>Instant searchable Archives with OCR</li>
        <li><svg class="tick" style="color:var(--dig)"><use href="#tick"/></svg>Automated Document Classification</li>
        <li><svg class="tick" style="color:var(--dig)"><use href="#tick"/></svg>Quorvane and Cloud Blob Ready</li>
      </ul>
    </div>
    <div class="art" role="img" aria-label="Faint line illustration of a monitor showing a chart and circuit lines"></div>
    <a class="btn" href="#">LEARN MORE</a>
  </section>

  <div class="hub-ring"></div>
  <div class="hub"><p class="hub-label">Super<br>Product</p></div>
</main>
</body>
</html>
```